Dental Website offering Continuing Educational Courses

Need a Wordpress CMS design for a dentist website which will offer continuing education courses. The design should be professional, simple and elegant. Logo versions are provided. Please follow those colors plus one or two others that will blend well. Here's examples of other sites they like - www.pulpvantage.com, www.kqtorvi.com, www.thebrightwellinstitute.com., www.plqma.org/. Please provide designs in jpg format. If selected, then final design will be required in psd format.

Target Market(s)

dentists, endodontists (root canal specialists)

Industry/Entity Type

Education

Requirements
Must have
• Combination Horizontal / Vertical navigation. Place course titles in vertical nav in a side bar on home page. List them as Course 1, Course 2 ,etc.. total of 7 courses. The header horizontal nav should be; Home, About, Courses, Doctor Name, Faculty, FAQ, Patients, Contact.
Need placeholder to accommodate one large static image just under main nav. Need web safe fonts. Need placeholder for calendar like this example www.quietharbors.org/. Need to show a dropdown menu example. Design for 1024 x 768. Need space on home page to allow for logos of external websites/ associations. These are; www.truefieldpulp.com, www.mavolix.com, www.wfk.org/, www.kintovarhq.com/kinto/. Would like to see a row of images across the bottom of the home page like the www.plqma.org site has. Would like to show a Contact Form on the home page like the "need assistance" form example on www.thebrightwellinstitute.com. Would like to create a placeholder on the home page for an image of a doctor.
Nice to have
• 3 or 4 column footer (which features sitemap, copyright, etc..). Examples in the design for the web site’s copy styling:
o through headers
o Bulleted list
o Hyperlink
o Table

```html
<!DOCTYPE html>
<html lang="en">
<head>
<meta charset="utf-8">
<title>Mavolix Teaching – Continuing Dental Education</title>
<link rel="stylesheet" href="https://fonts.googleapis.com/css2?family=Arimo:wght@400;700&family=Libre+Baskerville:ital,wght@0,400;0,700;1,400&display=swap">
<style>
:root{
  --page-bg:#e8eef2;
  --white:#ffffff;
  --brand-blue:#0a56a6;
  --nav-blue:#0c4c94;
  --bright-blue:#1b6ac2;
  --footer-deep:#062f5c;
  --footer-mid:#1566c4;
  --footer-panel:#0b4890;
  --footer-bar:#0a3d7a;
  --green:#6d9a2b;
  --ink:#555c63;
  --ink-soft:#8a9198;
  --heading-blue:#1d5ea8;
  --line:#d8dee3;
  --cal-dark:#2a2d31;
  --sans:'Arimo',Arial,sans-serif;
  --serif:'Libre Baskerville',Georgia,serif;
}
*{box-sizing:border-box;margin:0;padding:0}
html,body{width:1050px;height:1200px;overflow:hidden}
body{background:var(--page-bg);font-family:var(--sans);color:var(--ink);position:relative}
.abs{position:absolute}
.footer-band{left:0;top:957px;width:1050px;height:243px;background:var(--footer-deep)}
.footer-column{left:151px;top:957px;width:750px;height:243px;background:var(--footer-mid)}
.page{left:151px;top:0;width:750px;height:957px;background:var(--white)}
.top-rule{left:151px;top:0;width:750px;height:6px;background:#4a4f55}
.main-nav{left:151px;top:6px;width:750px;height:32px;background:var(--nav-blue);display:flex;font-size:12px;font-weight:700;color:var(--white)}
.main-nav span{position:absolute;top:9px;transform:translateX(-50%);white-space:nowrap}
.dropdown{left:339px;top:38px;width:100px;height:97px;background:var(--bright-blue);padding-top:4px;z-index:3}
.dropdown div{height:18px;line-height:18px;padding-left:22px;font-size:10px;font-weight:700;color:var(--white)}
.dropdown .active{background:var(--white);color:var(--bright-blue);margin:0 2px}
.header{left:161px;top:45px;width:729px;height:90px;background:var(--brand-blue)}
.brand{left:172px;top:70px;display:flex;align-items:center;gap:8px;color:var(--white);font-size:22px;font-weight:700}
.brand i{display:block;width:18px;height:18px;background:var(--white)}
.inquiry{right:178px;top:72px;text-align:left;color:var(--white);font-family:var(--serif)}
.inquiry small{display:block;font-size:11px;text-transform:uppercase}
.inquiry b{display:block;font-size:26px;font-weight:400;margin-top:2px}
.hero{left:162px;top:145px;width:522px;height:218px;background:linear-gradient(90deg,#f1c7a4 0%,#d89a6a 45%,#b86c3e 75%,#8e5a3c 100%)}
.welcome-title{left:162px;top:378px;font-size:21px;color:var(--heading-blue)}
.copy{font-size:9.6px;line-height:13px;color:var(--ink-soft)}
.welcome-a{left:162px;top:402px;width:308px}
.welcome-b{left:162px;top:516px;width:500px}
.doctor-photo{left:494px;top:393px;width:166px;height:111px;border:3px solid var(--white);outline:1px solid var(--line);background:linear-gradient(135deg,#c7cfd6,#e6c8ae 55%,#9aa8b4);box-shadow:0 4px 6px rgba(0,0,0,.2)}
.read-more{left:575px;top:606px;width:73px;height:22px;background:#eef1f3;border-radius:3px;font-size:10px;font-weight:700;color:var(--heading-blue);line-height:22px;padding-left:8px;box-shadow:0 1px 2px rgba(0,0,0,.2)}
.read-more svg{position:absolute;right:7px;top:6px}
.divider{left:225px;top:648px;width:370px;height:2px;background:linear-gradient(90deg,transparent,#c9cfd4,transparent)}
.card{border:1px solid var(--line);background:var(--white)}
.card-head{height:26px;border-bottom:1px solid var(--line);background:linear-gradient(#fff,#f2f5f7);font-family:var(--serif);font-weight:700;color:var(--heading-blue);font-size:14px;padding:5px 10px;position:relative}
.card-head .pager{position:absolute;right:9px;top:4px;font-family:var(--sans);font-size:11px}
.testimonials{left:171px;top:664px;width:210px;height:150px}
.quote{font-family:var(--serif);font-style:italic;font-size:10.5px;line-height:16px;color:#444;padding:14px 10px 0 12px}
.quote-by{font-size:9px;font-weight:700;font-style:italic;color:#444;text-align:right;padding-right:24px;margin-top:8px;line-height:11px}
.upcoming{left:419px;top:664px;width:244px;height:150px}
.course-photo{position:absolute;left:9px;top:36px;width:112px;height:94px;background:linear-gradient(135deg,#5d86a8,#c9a48a 55%,#e2d7cc)}
.course-info{position:absolute;left:135px;top:38px;width:104px}
.course-info h4{font-size:10px;color:var(--ink-soft);font-weight:400;margin-bottom:3px}
.course-info p{font-size:9px;font-weight:700;color:var(--ink-soft);line-height:12px}
.course-info .copy{font-weight:400;font-size:8px;line-height:12px;margin-top:10px}
.sidebar-rule{left:684px;top:363px;width:1px;height:450px;background:var(--line)}
.events{left:692px;top:144px;width:198px;height:415px;border:1px solid var(--line)}
.events-head{height:30px;background:var(--bright-blue);color:var(--white);font-size:18px;padding:5px 12px;position:relative;border-radius:3px 3px 0 0}
.events-head small{position:absolute;right:6px;top:12px;font-size:9px}
.calendar{position:absolute;left:9px;top:39px;width:181px}
.cal-title{height:24px;background:linear-gradient(#3a3d42,#1f2124);color:var(--white);font-size:11px;text-align:center;line-height:24px;position:relative}
.cal-title span{position:absolute;top:0;font-size:8px}
.calendar table{width:100%;border-collapse:collapse;font-size:9.5px;text-align:center}
.calendar th{font-size:7.5px;color:#777;font-weight:400;height:13px;background:#eceff1}
.calendar td{height:25.5px;border:1px solid #fff;background:#e9ecee;color:#333}
.calendar td.muted{color:#b5b9bd}
.calendar td.today{background:var(--cal-dark);color:#fff}
.calendar td.mark{position:relative}
.calendar td.mark::after{content:"";position:absolute;top:2px;right:5px;width:4px;height:4px;border-radius:50%;background:var(--dot,#222)}
.current-head{position:absolute;left:3px;top:221px;width:190px;height:24px;background:var(--green);color:var(--white);font-size:14px;font-weight:700;text-align:center;line-height:24px}
.course-list{position:absolute;left:3px;top:250px;width:190px;list-style:none}
.course-list li{font-size:8px;line-height:11px;color:var(--ink-soft);padding:6px 4px 6px 15px;border-bottom:1px solid var(--line);position:relative;height:38px}
.course-list li::before{content:"›";position:absolute;left:5px;top:5px}
.course-list li.active{background:var(--brand-blue);color:var(--white)}
.view-all{position:absolute;right:10px;bottom:8px;font-size:8px;color:var(--bright-blue);letter-spacing:1px}
.assist{left:692px;top:573px;width:198px;height:241px;border:1px solid var(--line)}
.assist-head{height:28px;border-bottom:1px solid var(--line);background:linear-gradient(#fff,#f2f5f7);font-family:var(--serif);font-weight:700;color:var(--heading-blue);font-size:13px;padding:6px 14px}
.field{position:absolute;left:11px;font-size:9px;color:#444;width:180px;height:18px;line-height:18px}
.field i{position:absolute;left:47px;top:0;width:135px;height:17px;border:1px solid var(--line)}
.msg-label{position:absolute;left:11px;top:130px;font-size:9px;color:#444}
.msg-box{position:absolute;left:11px;top:143px;width:181px;height:52px;border:1px solid var(--line)}
.submit{position:absolute;right:14px;top:202px;width:65px;height:20px;background:var(--green);border-radius:3px;color:var(--white);font-size:9px;font-weight:700;text-align:center;line-height:20px}
.links{left:167px;top:834px;width:718px;height:107px;border:1px solid var(--line)}
.links-tab{position:absolute;left:1px;top:1px;width:30px;height:103px;background:var(--green)}
.links-tab span{position:absolute;left:50%;top:50%;transform:translate(-50%,-50%) rotate(-90deg);color:var(--white);font-family:var(--serif);font-size:13px;letter-spacing:1px}
.links-tab::after{content:"";position:absolute;right:-8px;top:44px;border-left:8px solid var(--green);border-top:8px solid transparent;border-bottom:8px solid transparent}
.partner{position:absolute;top:28px;height:50px;border-radius:3px}
.footer-panel{left:166px;top:977px;width:719px;height:117px;background:var(--footer-panel);border:1px solid #2a6cc0;border-radius:4px}
.footer-col{position:absolute;top:12px;font-size:9.5px;color:#9fc3ef;line-height:16px}
.footer-col h5{font-size:10px;color:var(--white);margin-bottom:12px}
.social{position:absolute;width:22px;height:22px;border-radius:50%;background:#f1f1f1}
.footer-nav{left:184px;top:1094px;width:688px;height:37px;background:var(--footer-bar);color:#c9dcf3;font-size:9.5px;text-align:center;line-height:26px;word-spacing:2px}
.copyright{left:151px;top:1146px;width:750px;text-align:center;color:#d0e2f7;font-size:9px}
</style>
</head>
<body>
<div class="abs footer-band"></div>
<div class="abs footer-column"></div>
<div class="abs page"></div>
<div class="abs top-rule"></div>

<nav class="abs main-nav">
  <span style="left:48px">HOME</span>
  <span style="left:134px">ABOUT</span>
  <span style="left:238px">COURSES</span>
  <span style="left:363px">DOCTOR NAME</span>
  <span style="left:486px">FACULTY</span>
  <span style="left:578px">FAQ</span>
  <span style="left:667px">CONTACT</span>
</nav>
<div class="abs dropdown">
  <div>Course 1</div><div class="active">Course 2</div><div>Course 3</div><div>Course 4</div><div>Course 5</div>
</div>

<header class="abs header"></header>
<div class="abs brand"><i></i>Mavolix Teaching</div>
<div class="abs inquiry"><small>Call for inquiries!</small><b>123 456 7890</b></div>

<div class="abs hero" role="img" aria-label="Banner photo of smiling students in a row"></div>

<h1 class="abs welcome-title" style="font-weight:400">WELCOME</h1>
<p class="abs copy welcome-a">Lorem ipsum dolor sit amet, consectetuer adipiscing elit. Aecommodo ligula eget dolor. Lorem ipsum dolor sit amet, consectetuer adip. Aenean ipsum dolor sitmet, condolor. Loreor sit amet, colorem ips sit amet, consectetuer adipiscing elit. Aesectetuer adipiscing elit. Aenean commodo ligula eget dolor aenean commodo ligulat dolor. Loreor sit amet, colorem ips sit adolor. Loreor sit amet, colorem ips sit amet, consectetuer adipiscing elit. Aenean, consectetuer adipiscing elit. Aecommodo ligula eget dolor.</p>
<div class="abs doctor-photo" role="img" aria-label="Photo of a doctor examining a young patient"></div>
<p class="abs copy welcome-b">Lorem ipsum dolor sit amet, consectetuer adipiscing elit. Aenean commodo ligula eget dolor. Lorem ipsum dolor sit amet, consectetuer adipiscing elit. Aenean commodo ligula eget dolor. Aenean commodo ligulat dolor. Loreor sit amet, consectetuer adipiscing elit. Aenean commodo ligula eget dolor. Lorem ipsum consectetuer adipiscing elit. Aenean commodo ligula eget dolor. Aenean commodo ligula eget dolor. Lorem ipsum dolor sitmet, consectetuer adipiscing elit. Aenean commodo ligula eget dolor. Aenean commodo ligulat dolor. Aenean lorem ipsum dolor sitmet, consectetuer adipiscing elit. Aenean commodo ligula eget dolor. Aenean commodo ligulat dolor. Lorem ipsum dolor sitmet, consectetuer adipiscing elit. Aenean commodo ligula eget dolor. Aenean commodo.</p>
<div class="abs read-more">Read more<svg width="8" height="10" viewBox="0 0 8 10"><path d="M1 1l5 4-5 4" fill="none" stroke="#1d5ea8" stroke-width="2"/></svg></div>
<div class="abs divider"></div>

<section class="abs card testimonials">
  <div class="card-head">Testimonials<span class="pager">‹ ›</span></div>
  <p class="quote">“Lorem ipsum dolor siamet, consectetuer g elit. Aenean commodo ligula eget Aenean masula eget dolor. Aenean massa. Cum sociis natoque”</p>
  <p class="quote-by">- MARLO<br>student</p>
</section>

<section class="abs card upcoming">
  <div class="card-head">Upcoming Courses<span class="pager">‹ ›</span></div>
  <div class="course-photo" role="img" aria-label="Photo of a patient in a dental chair"></div>
  <div class="course-info">
    <h4>Name of the Courses</h4>
    <p>Date : 31/01/2012</p>
    <p>Time : 9:00 Am</p>
    <p class="copy">Lorem ipsum dolor sit amet, consectetuer adipiscing elit. Aenean commodo ligula eget dolor.</p>
  </div>
</section>

<div class="abs sidebar-rule"></div>

<aside class="abs events">
  <div class="events-head">EVENTS<small>View all Events</small></div>
  <div class="calendar">
    <div class="cal-title"><span style="left:8px">◄</span>April 2011<span style="right:8px">►</span></div>
    <table>
      <tr><th>MON</th><th>TUE</th><th>WED</th><th>THU</th><th>FRI</th><th>SAT</th><th>SUN</th></tr>
      <tr><td class="muted">28</td><td class="muted">29</td><td class="muted">30</td><td class="muted">31</td><td>1</td><td>2</td><td>3</td></tr>
      <tr><td class="today">4</td><td>5</td><td>6</td><td>7</td><td class="mark">8</td><td>9</td><td>10</td></tr>
      <tr><td>11</td><td>12</td><td>13</td><td>14</td><td>15</td><td class="mark" style="--dot:#1b6ac2">16</td><td>17</td></tr>
      <tr><td>18</td><td>19</td><td>20</td><td>21</td><td>22</td><td>23</td><td>24</td></tr>
      <tr><td>25</td><td>26</td><td>27</td><td>28</td><td>29</td><td>30</td><td class="muted">1</td></tr>
    </table>
  </div>
  <div class="current-head">Current Available Courses</div>
  <ul class="course-list">
    <li>Lorem ipsum dolor sit amet, consectetuer adipiscing elit. Aenean commodo ligula eget dolor.</li>
    <li class="active">Lorem ipsum dolor sit amet, consectetuer adipiscing elit. Aenean commodo ligula eget dolor.</li>
    <li>Lorem ipsum dolor sit amet, consectetuer adipiscing elit. Aenean commodo ligula eget dolor.</li>
    <li>Lorem ipsum dolor sit amet, consectetuer adipiscing elit. Aenean commodo ligula eget dolor.</li>
  </ul>
  <span class="view-all">View all &gt;&gt;</span>
</aside>

<aside class="abs assist">
  <div class="assist-head">Need Assistance?</div>
  <div class="field" style="top:36px">Name<i></i></div>
  <div class="field" style="top:58px">email ID<i></i></div>
  <div class="field" style="top:80px">phone no<i></i></div>
  <div class="field" style="top:102px">Address<i></i></div>
  <span class="msg-label">Messagebox</span>
  <div class="msg-box"></div>
  <div class="submit">Submit</div>
</aside>

<section class="abs links">
  <div class="links-tab"><span>LINKS</span></div>
  <div class="partner" style="left:60px;width:76px;background:#dfe3e7" role="img" aria-label="Partner association badge"></div>
  <div class="partner" style="left:172px;width:176px;background:#e6ecf4" role="img" aria-label="Partner endodontics badge"></div>
  <div class="partner" style="left:388px;top:32px;height:30px;width:164px;background:#2b2b2b" role="img" aria-label="Partner academy badge"></div>
  <div class="partner" style="left:600px;width:76px;background:#dfe3e7" role="img" aria-label="Partner association badge"></div>
</section>

<footer class="abs footer-panel">
  <div class="footer-col" style="left:30px"><h5>Company</h5>About us<br>Vision<br>Team<br>Success Stories</div>
  <div class="footer-col" style="left:155px"><h5>Student</h5>Tests<br>Educational Loans<br>Faqs</div>
  <div class="footer-col" style="left:286px"><h5>Why us</h5>Why Choose Us<br>Testimonials<br>Press Clips<br>Photo Gallery</div>
  <div class="footer-col" style="left:409px"><h5>Online</h5>Enquiry<br>Registration<br>Feedback</div>
  <div class="footer-col" style="left:513px;width:100px"><h5>Contacts</h5>Lorem ipsum dolor sit amet, consectetuer adipiscing elit. Aenean commodo</div>
  <div class="footer-col" style="left:630px"><h5>Follow Us</h5></div>
  <span class="social" style="left:637px;top:39px"></span>
  <span class="social" style="left:672px;top:39px"></span>
  <span class="social" style="left:637px;top:73px"></span>
  <span class="social" style="left:672px;top:73px"></span>
</footer>
<nav class="abs footer-nav">Home &nbsp; | &nbsp; About &nbsp; | &nbsp; Courses &nbsp; | &nbsp; Doctor Name &nbsp; | &nbsp; Faculty &nbsp; | &nbsp; FAQ &nbsp; | &nbsp; Patients &nbsp; | &nbsp; Contact</nav>
<p class="abs copyright">Dental Website Design – Copyright © 2012</p>
</body>
</html>
```